Law Offices business card

Hi there, I'll need business card for the Law Offices of Colin Matheny. The information must convey his strategic approach and quick resolution to complex business litigation needs. Please emphasize Civil Litigation, Corporate Law, Business Governance and Real Estate Law. Colin has over 25 years of experience in these fields.The card should be modern and edgy and the message should be clear. Please consult his current website for ideas.

```html
<!DOCTYPE html>
<html lang="en">
<head>
<meta charset="utf-8">
<title>Law Offices of Colin Matheny – Business Card</title>
<link href="https://fonts.googleapis.com/css2?family=Arimo:wght@400;700&family=Tinos:wght@400;700&display=swap" rel="stylesheet">
<style>
  :root {
    --backdrop: #e9e6e2;
    --front-light: #d6d6d4;
    --front-mid: #a9a9a7;
    --front-dark: #6f6f6d;
    --ink: #111111;
    --back-bg: #000000;
    --back-frame: #7a7a78;
    --back-text: #ffffff;
    --emblem: #141414;
  }
  * { margin: 0; padding: 0; box-sizing: border-box; }
  html, body {
    width: 1189px; height: 1200px; overflow: hidden;
    background: var(--backdrop);
  }
  .canvas { position: relative; width: 1189px; height: 1200px; }

  .card {
    position: absolute; left: 140px; width: 918px; height: 522px;
    text-align: center;
  }
  .card-front {
    top: 46px;
    border: 9px solid var(--ink);
    background: radial-gradient(ellipse at 50% 45%, var(--front-light) 0%, var(--front-mid) 60%, var(--front-dark) 100%);
    color: var(--ink);
  }
  .card-back {
    top: 624px;
    border: 9px solid var(--back-frame);
    background: var(--back-bg);
    color: var(--back-text);
    overflow: hidden;
  }

  .line { position: absolute; left: 0; right: 0; }
  .name {
    top: 58px; font-family: "Tinos", serif; font-weight: 700;
    font-size: 52px; letter-spacing: 0.5px;
  }
  .title {
    top: 124px; font-family: "Arimo", sans-serif; font-weight: 700;
    font-size: 39px;
  }
  .divider {
    position: absolute; top: 200px; left: 73px; width: 769px;
    height: 3px; background: var(--ink);
  }
  .firm {
    top: 233px; font-family: "Tinos", serif; font-weight: 700;
    font-size: 36px; letter-spacing: 0.3px;
  }
  .contact {
    font-family: "Arimo", sans-serif; font-size: 25px;
  }
  .c1 { top: 316px; } .c2 { top: 355px; } .c3 { top: 394px; }
  .c4 { top: 432px; } .c5 { top: 469px; }

  .emblem-area {
    position: absolute; left: 2px; top: 52px; width: 458px; height: 460px;
    background: radial-gradient(ellipse at 50% 50%, var(--emblem) 0%, var(--back-bg) 75%);
  }
  .services-heading {
    top: 97px; font-family: "Tinos", serif; font-weight: 700;
    font-size: 58px;
  }
  .service {
    font-family: "Arimo", sans-serif; font-size: 31px;
  }
  .s1 { top: 273px; } .s2 { top: 333px; } .s3 { top: 394px; }
</style>
</head>
<body>
<main class="canvas">
  <section class="card card-front">
    <h1 class="line name">Colin Matheny</h1>
    <p class="line title">Attorney</p>
    <div class="divider"></div>
    <p class="line firm">Law Offices of Colin Matheny, P.A.</p>
    <p class="line contact c1">561-555-0148</p>
    <p class="line contact c2">561-555-0193</p>
    <p class="line contact c3">colin@colinlaw.com</p>
    <p class="line contact c4">www.colinlaw.com</p>
    <p class="line contact c5">314C Coral Avenue, Bay Harbor, Florida 33154</p>
  </section>

  <section class="card card-back">
    <div class="emblem-area" role="img" aria-label="Faint scales of justice emblem"></div>
    <h2 class="line services-heading">Srevices</h2>
    <p class="line service s1">Civil Litigation</p>
    <p class="line service s2">Corporate Law</p>
    <p class="line service s3">Business Governance and Real Estate Law</p>
  </section>
</main>
</body>
</html>
```